Redesign to improve branding visibility and product messaging

Update the logo using the new logo provided attached.
Then, improve product messaging on the packaging, however leaving the colours, general blurbs, and the fruit/nut image outlines as they are (but open to make it simpler).
Please review photos Stockist 1" to 5" and recommend the new style for:
1 Energy Ball Bag
1 Energy Ball Inner Box
1 Cereal Bag
Key features:
1. Allow more transparent window to show more of the product inside.
2. Strong brand presence and clear nutritional call outs - keep in mind we display our products on supermarket shelves.
3. Product Messaging:
- 1st priority: Product Name
- 2nd priority: Nutritional call outs (All natural, GF, Vegan, High Fibre, No added sugar, etc.). This info is available in the current packaging and more info on the website.
- 3rd priority: Ingredients on front cover (example: 7 ingredients only: x1, x2, x3, x4, x5, x6, x7.)
- 4th priority: Locally Made by a nutritionist.
- 5th priority: Sugar content in the nutritional panel to say: From Healthy Natural Sources
Tips:
1. Use Style 1 as benchmark.
2. Use the other image references as follows:
Style 2 and 5 = Try do something similar for the energy ball bags.
Style 4 = Maybe add the line up of other flavours on the back or the side of the packaging for the energy ball box and the cereal bags.
Style 7 = Do something similar with regards to the use of real imagery on the packaging as if you can pick out the product right of the packaging. Note also how they list the ingredients on the front of packaging.
Style 8 = Do something similar - be proud about the real ingredients used.
Style 9 = An example of how much transparent area we can do, please suggest a nice unique transparent shape.
Style 10 = copy the way it communicates the health benefits very clearly.

```html
<!DOCTYPE html>
<html lang="en">
<head>
<meta charset="utf-8">
<title>Bramble Nutrition – Maple &amp; Vanilla Granola packaging</title>
<link href="https://fonts.googleapis.com/css2?family=Oswald:wght@500;700&family=Roboto:wght@400;500;700&display=swap" rel="stylesheet">
<style>
:root{
  --stage:#f7b3cf;
  --plum:#7a1348;
  --berry:#c2306f;
  --pink:#e6639c;
  --pink-soft:#f3b6cf;
  --blush:#fbe3ee;
  --window:#ff63ad;
  --white:#ffffff;
  --ink:#5a1036;
  --outline:#d84c88;
}
*{box-sizing:border-box;margin:0;padding:0}
html,body{width:1200px;height:720px;overflow:hidden;background:var(--stage)}
body{position:relative;font-family:"Roboto",Arial,sans-serif;color:var(--plum)}

/* Inner box dieline */
.dieline{position:absolute;left:18px;top:165px;width:620px;height:390px;filter:drop-shadow(0 4px 8px rgba(122,19,72,.18))}
.dieline text{fill:var(--plum)}
.dl-title{font-family:"Oswald",Impact,sans-serif;font-weight:700}
.dl-brand{font-family:"Oswald",Impact,sans-serif;font-weight:700;fill:var(--white)}
.dl-small{font-family:"Roboto",Arial,sans-serif;font-size:3.6px}
.dl-label{font-family:"Roboto",Arial,sans-serif;font-weight:700;font-size:4px}

/* Flat artwork panels */
.panel{position:absolute;border-radius:26px;overflow:hidden;transform-origin:left top;
  background:linear-gradient(180deg,var(--pink) 0%,var(--pink-soft) 45%,var(--blush) 72%,var(--white) 100%);
  box-shadow:0 6px 18px rgba(122,19,72,.18)}
.panel--bar{left:652px;top:162px;width:390px;height:600px;transform:scale(.66)}
.panel--cereal{left:913px;top:162px;width:455px;height:660px;transform:scale(.6)}

.deco{position:absolute;border-radius:50%}
.deco--berry{background:radial-gradient(circle,#d93c77 0%,#e86a9b 70%,rgba(232,106,155,0) 100%);opacity:.75}
.deco--nut{border:2px solid var(--outline);opacity:.45;border-radius:50% 50% 50% 50% / 60% 60% 40% 40%}
.deco--seeds{background:radial-gradient(circle,rgba(200,40,105,.55),rgba(200,40,105,0) 70%)}
.deco--slice{border:3px solid rgba(216,76,136,.35);background:rgba(255,255,255,.12)}

.title{font-family:"Oswald",Impact,sans-serif;font-weight:700;color:var(--plum);line-height:.98;text-transform:uppercase}
.subtitle{font-size:9px;color:var(--plum);letter-spacing:.2px}
.brand{font-family:"Oswald",Impact,sans-serif;font-weight:700;color:var(--white);text-transform:uppercase;line-height:1;display:flex;flex-direction:column;align-items:flex-start;gap:2px}
.brand__name{display:flex;align-items:center;gap:6px}
.brand__dot{width:14px;height:14px;border-radius:50%;background:var(--white);flex:none}
.claims{display:flex;gap:8px;align-items:center}
.claim{display:flex;align-items:center;gap:4px;font-size:8.5px;font-weight:500;line-height:1.1;color:var(--plum)}
.claim svg{flex:none}
.claim--stacked{flex-direction:column;text-align:center;font-size:9px;font-weight:700}
.upside{position:absolute;left:0;top:14px;width:100%;transform:rotate(180deg);text-align:center}
.upside__blurb{font-size:8.5px;line-height:1.35;color:var(--plum);text-transform:uppercase;padding:0 40px}
.upside__join{font-family:"Oswald",sans-serif;font-weight:500;font-size:13px;line-height:1.15;color:var(--plum);margin-top:8px}
.socials{display:flex;justify-content:center;gap:6px;margin-top:6px}
.social{background:var(--plum);color:var(--white);font-size:8px;font-weight:700;border-radius:8px;padding:3px 10px;display:flex;align-items:center;gap:4px}
.social i{width:7px;height:7px;border-radius:50%;background:var(--white);display:inline-block}
.benefits-line{font-size:8.5px;font-weight:500;line-height:1.2;border-left:1px solid var(--plum);padding-left:6px}
.net-vertical{position:absolute;font-family:"Oswald",sans-serif;font-weight:500;font-size:11px;transform:rotate(-90deg);transform-origin:left top}
.nutrition{position:absolute;border-collapse:collapse;font-size:5.5px;color:var(--ink)}
.nutrition th,.nutrition td{padding:1.2px 3px;border-bottom:.5px solid var(--ink);text-align:right}
.nutrition th:first-child,.nutrition td:first-child{text-align:left}
.nutrition caption{text-align:left;font-weight:700;font-size:5.5px;border-bottom:1px solid var(--ink);padding-bottom:1px}
.fine{position:absolute;font-size:6px;line-height:1.35;color:var(--ink)}
.fine b{font-size:6.5px}
.badge{position:absolute;background:#fff;border:1.5px solid #2f8a45;border-radius:3px}
.stamp{position:absolute;border:1.5px dashed var(--plum);border-radius:50%}
.blurb{position:absolute;font-size:7.5px;line-height:1.28;text-transform:uppercase;color:var(--ink);text-align:justify}
.benefits{position:absolute;font-size:8px;line-height:1.35;color:var(--ink)}
.benefits h4{font-size:9px;font-weight:700;margin-bottom:1px}
.benefits ul{list-style:none;display:grid;grid-template-columns:1fr 1fr;column-gap:14px}
.benefits li::before{content:"• "}
.net{position:absolute;font-size:10px;font-weight:700;color:var(--ink)}
</style>
</head>
<body>

<!-- Energy ball inner box, flat dieline -->
<svg class="dieline" viewBox="0 0 620 390" role="group" aria-label="Energy ball inner box dieline">
  <defs>
    <linearGradient id="tallFill" x1="0" y1="0" x2="0" y2="1">
      <stop offset="0" stop-color="#e6639c"/>
      <stop offset=".32" stop-color="#f3b6cf"/>
      <stop offset=".5" stop-color="#f8d2e2"/>
      <stop offset=".53" stop-color="#e6639c"/>
      <stop offset=".66" stop-color="#fbe3ee"/>
      <stop offset=".72" stop-color="#ffffff"/>
    </linearGradient>
    <linearGradient id="faceFill" x1="0" y1="0" x2="0" y2="1">
      <stop offset="0" stop-color="#e6639c"/>
      <stop offset=".55" stop-color="#f6c6da"/>
      <stop offset="1" stop-color="#ffffff"/>
    </linearGradient>
    <linearGradient id="flapFill" x1="0" y1="0" x2="0" y2="1">
      <stop offset="0" stop-color="#d94a88"/>
      <stop offset="1" stop-color="#e6639c"/>
    </linearGradient>
  </defs>

  <!-- die shapes -->
  <path d="M0 205 L15 205 L15 255 L0 250 Z" fill="#f0a6c6"/>
  <path d="M15 10 Q15 0 25 0 L123 0 Q133 0 133 10 L133 390 L96 390 L96 345 L64 345 L64 390 L15 390 Z" fill="url(#tallFill)"/>
  <!-- front face -->
  <path d="M140 205 L146 122 Q147 112 157 112 L288 112 L316 185 L316 205 Z" fill="url(#flapFill)"/>
  <rect x="133" y="205" width="183" height="55" fill="url(#faceFill)"/>
  <path d="M133 260 L316 260 L316 298 L226 298 L218 280 L133 280 Z" fill="#ffffff"/>
  <!-- side -->
  <path d="M316 199 L437 205 L437 260 L316 260 Z" fill="url(#faceFill)"/>
  <path d="M316 260 L437 260 L437 280 L410 280 L405 390 Q375 400 350 390 L345 280 L316 280 Z" fill="#ffffff"/>
  <!-- back face -->
  <path d="M437 205 L445 122 Q446 112 456 112 L605 112 Q615 112 616 122 L620 205 Z" fill="url(#flapFill)"/>
  <rect x="437" y="205" width="183" height="55" fill="url(#faceFill)"/>
  <path d="M437 260 L620 260 L620 280 L538 280 L530 298 L468 298 L462 280 L437 280 Z" fill="#ffffff"/>

  <!-- fruit and nut outline areas -->
  <g role="img" aria-label="cranberry and almond outline illustrations">
    <circle cx="24" cy="40" r="8" fill="#d93c77" opacity=".7"/>
    <circle cx="128" cy="26" r="10" fill="#d93c77" opacity=".55"/>
    <circle cx="128" cy="80" r="6" fill="#d93c77" opacity=".6"/>
    <circle cx="30" cy="100" r="12" fill="#d84c88" opacity=".25"/>
    <circle cx="140" cy="255" r="7" fill="#d93c77" opacity=".7"/>
    <circle cx="440" cy="256" r="7" fill="#d93c77" opacity=".7"/>
    <ellipse cx="255" cy="213" rx="16" ry="7" fill="#d84c88" opacity=".3"/>
    <ellipse cx="565" cy="210" rx="14" ry="8" fill="none" stroke="#d84c88" stroke-width="1" opacity=".5"/>
    <circle cx="310" cy="220" r="9" fill="#d84c88" opacity=".25"/>
    <circle cx="445" cy="214" r="8" fill="#f3b6cf" opacity=".8"/>
  </g>

  <!-- tall back panel: upside-down title and brand -->
  <g transform="rotate(180 74 45)">
    <text class="dl-title" x="74" y="58" font-size="14" text-anchor="middle">MAPLE &amp; VANILLA</text>
    <text class="dl-title" x="74" y="72" font-size="14" text-anchor="middle">GRANOLA</text>
    <text class="dl-small" x="74" y="79" text-anchor="middle">WITH COCONUT &amp; DRIED CRANBERRIES</text>
  </g>
  <g transform="rotate(180 74 92)">
    <circle cx="54" cy="90" r="3" fill="#fff"/>
    <text class="dl-brand" x="60" y="93" font-size="9">BRAMBLE</text>
    <text class="dl-brand" x="60" y="99" font-size="5" letter-spacing=".6">NUTRITION</text>
  </g>
  <circle cx="66" cy="128" r="2.5" fill="#fff"/>
  <text class="dl-brand" x="70" y="130" font-size="6">BRAMBLE</text>
  <text class="dl-brand" x="70" y="135" font-size="3.6" letter-spacing=".4">NUTRITION</text>

  <!-- nutrition panel -->
  <g>
    <text class="dl-label" x="20" y="146">THE GOODNESS YOU'RE RECEIVING</text>
    <line x1="20" y1="148" x2="68" y2="148" stroke="#5a1036" stroke-width=".6"/>
    <text class="dl-small" x="20" y="153">Energy</text><text class="dl-small" x="48" y="153">752kJ</text><text class="dl-small" x="60" y="153">1880kJ</text>
    <text class="dl-small" x="20" y="158">Protein</text><text class="dl-small" x="48" y="158">3.3g</text><text class="dl-small" x="60" y="158">8.2g</text>
    <text class="dl-small" x="20" y="163">Fat, Total</text><text class="dl-small" x="48" y="163">13.2g</text><text class="dl-small" x="60" y="163">33.0g</text>
    <text class="dl-small" x="20" y="168">Carbs</text><text class="dl-small" x="48" y="168">9.9g</text><text class="dl-small" x="60" y="168">24.8g</text>
    <text class="dl-small" x="20" y="173">Sugars</text><text class="dl-small" x="48" y="173">9.7g</text><text class="dl-small" x="60" y="173">24.2g</text>
    <text class="dl-small" x="20" y="178">Fibre</text><text class="dl-small" x="48" y="178">5.6g</text><text class="dl-small" x="60" y="178">14g</text>
    <text class="dl-small" x="20" y="183">Sodium</text><text class="dl-small" x="48" y="183">8mg</text><text class="dl-small" x="60" y="183">20mg</text>
    <text class="dl-label" x="73" y="146">THE GOODNESS</text>
    <text class="dl-label" x="73" y="150.5">YOU'RE EATING</text>
    <text class="dl-small" x="73" y="156">Dried Apricot (37%),</text>
    <text class="dl-small" x="73" y="160">Almond Meal (25%),</text>
    <text class="dl-small" x="73" y="164">Coconut (25%),</text>
    <text class="dl-small" x="73" y="168">Maple Syrup (7%)</text>
    <text class="dl-small" x="73" y="174">Made in Canberra</text>
    <rect x="73" y="178" width="34" height="8" rx="1" fill="#fff" stroke="#2f8a45" stroke-width=".8" role="img" aria-label="country of origin badge"/>
    <circle cx="114" cy="182" r="3.5" fill="none" stroke="#5a1036" stroke-width=".8"/>
  </g>

  <text class="dl-label" x="74" y="216" text-anchor="middle">JOIN US IN THE KITCHEN &amp;</text>
  <text class="dl-label" x="74" y="221" text-anchor="middle">VIEW MORE HEALTHY RECIPES:</text>
  <rect x="36" y="225" width="76" height="5" rx="1" fill="#7a1348"/>
  <text x="74" y="229" font-size="3.4" font-weight="700" fill="#fff" text-anchor="middle" font-family="Roboto,sans-serif">@BRAMBLENUTRITION</text>
  <rect x="36" y="232" width="76" height="5" rx="1" fill="#7a1348"/>
  <text x="74" y="236" font-size="3.4" font-weight="700" fill="#fff" text-anchor="middle" font-family="Roboto,sans-serif">@BRAMBLEKITCHEN</text>
  <text class="dl-small" x="74" y="274" text-anchor="middle">TO REFILL THIS BOX, PLEASE CONTACT</text>
  <text class="dl-label" x="74" y="279" text-anchor="middle">ORDERS@BRAMBLENUTRITION.COM.AU</text>

  <!-- front face -->
  <circle cx="148" cy="231" r="3.5" fill="#fff"/>
  <text class="dl-brand" x="154" y="234" font-size="10">BRAMBLE</text>
  <text class="dl-brand" x="154" y="241" font-size="5.5" letter-spacing=".6">NUTRITION</text>
  <text class="dl-title" x="202" y="229" font-size="15">MAPLE &amp;VANILLA</text>
  <text class="dl-title" x="202" y="245" font-size="15">GRANOLA</text>
  <text class="dl-small" x="202" y="251">WITH COCONUT &amp; DRIED CRANBERRIES</text>

  <!-- side panel -->
  <text class="dl-label" x="321" y="214">BENEFITS:</text>
  <text class="dl-small" x="321" y="219">• High fibre</text><text class="dl-small" x="352" y="219">• Sustained Energy</text>
  <text class="dl-small" x="321" y="223">• Digestive Support</text><text class="dl-small" x="352" y="223">• Antioxidants</text>
  <text class="dl-small" x="321" y="227">• Healthy fats</text><text class="dl-small" x="352" y="227">• Immunity</text>
  <text class="dl-small" x="321" y="233">Sweet, chewy &amp; delicious, filled</text>
  <text class="dl-small" x="321" y="237">with apricots, almonds, coconut.</text>
  <text class="dl-small" x="321" y="243">Made in small batches.</text>
  <circle cx="408" cy="216" r="6" fill="none" stroke="#7a1348" stroke-width=".7" stroke-dasharray="1.2 1" role="img" aria-label="locally made seal"/>
  <g fill="none" stroke="#7a1348" stroke-width=".8">
    <circle cx="390" cy="235" r="3"/><circle cx="400" cy="235" r="3"/><circle cx="410" cy="235" r="3"/><circle cx="420" cy="235" r="3"/>
  </g>
  <text x="390" y="243" font-size="2.8" fill="#7a1348" text-anchor="middle" font-family="Roboto,sans-serif">High</text>
  <text x="400" y="243" font-size="2.8" fill="#7a1348" text-anchor="middle" font-family="Roboto,sans-serif">GF</text>
  <text x="410" y="243" font-size="2.8" fill="#7a1348" text-anchor="middle" font-family="Roboto,sans-serif">Vegan</text>
  <text x="420" y="243" font-size="2.8" fill="#7a1348" text-anchor="middle" font-family="Roboto,sans-serif">No Sug</text>
  <text class="dl-label" x="398" y="252" text-anchor="middle">40G NET</text>

  <!-- back face -->
  <text class="dl-title" x="573" y="229" font-size="15" text-anchor="end">MAPLE &amp;VANILLA</text>
  <text class="dl-title" x="573" y="245" font-size="15" text-anchor="end">GRANOLA</text>
  <text class="dl-small" x="573" y="251" text-anchor="end">WITH COCONUT &amp; DRIED CRANBERRIES</text>
  <circle cx="580" cy="231" r="3" fill="#fff"/>
  <text class="dl-brand" x="585" y="234" font-size="8">BRAMBLE</text>
  <text class="dl-brand" x="585" y="240" font-size="4.4" letter-spacing=".4">NUTRITION</text>
</svg>

<!-- Energy ball bag artwork -->
<section class="panel panel--bar" aria-label="Energy ball bag artwork">
  <div class="deco deco--nut" style="left:20px;top:-14px;width:70px;height:42px" role="img" aria-label="almond outline illustration"></div>
  <div class="deco deco--seeds" style="left:140px;top:-10px;width:110px;height:40px" role="img" aria-label="seed scatter illustration"></div>
  <div class="deco deco--nut" style="left:320px;top:-10px;width:80px;height:50px" role="img" aria-label="almond outline illustration"></div>
  <div class="deco deco--seeds" style="left:320px;top:80px;width:70px;height:110px" role="img" aria-label="seed scatter illustration"></div>
  <div class="deco deco--slice" style="left:-30px;top:300px;width:70px;height:100px" role="img" aria-label="apricot slice outline illustration"></div>
  <div class="deco deco--slice" style="left:340px;top:210px;width:70px;height:100px" role="img" aria-label="apricot slice outline illustration"></div>
  <div class="deco deco--berry" style="left:340px;top:355px;width:54px;height:54px" role="img" aria-label="cranberry illustration"></div>
  <div class="deco deco--nut" style="left:200px;top:385px;width:30px;height:22px" role="img" aria-label="almond outline illustration"></div>
  <div class="deco deco--berry" style="left:320px;top:555px;width:80px;height:80px" role="img" aria-label="cranberry illustration"></div>

  <div class="upside">
    <p class="upside__blurb">Sweet, chewy &amp; delicious, our apricot &amp; coconut energy balls are filled with dried apricots, almonds, coconut &amp; a touch of maple syrup &amp; vanilla.<br>Made in small batches, &amp; full of fibre. These energy balls make for a deliciously healthy snack.</p>
    <p class="upside__join">JOIN US IN THE KITCHEN &amp;<br>VIEW MORE HEALTHY RECIPES:</p>
    <div class="socials">
      <span class="social"><i></i>@BRAMBLENUTRITION</span>
      <span class="social"><i></i>@BRAMBLEKITCHEN</span>
    </div>
  </div>

  <div class="claims" style="position:absolute;left:26px;top:186px">
    <span class="claim"><svg width="18" height="18" viewBox="0 0 18 18"><circle cx="9" cy="9" r="8" fill="none" stroke="currentColor" stroke-width="1.6"/><path d="M5 9.5l2.6 2.5L13 6.5" fill="none" stroke="currentColor" stroke-width="1.6"/></svg>Gluten<br>Free</span>
    <span class="claim"><svg width="18" height="18" viewBox="0 0 18 18"><circle cx="9" cy="9" r="8" fill="none" stroke="currentColor" stroke-width="1.6"/><path d="M5 9.5l2.6 2.5L13 6.5" fill="none" stroke="currentColor" stroke-width="1.6"/></svg>Vegan</span>
    <span class="claim"><svg width="18" height="18" viewBox="0 0 18 18"><circle cx="9" cy="9" r="8" fill="none" stroke="currentColor" stroke-width="1.6"/><path d="M5 9.5l2.6 2.5L13 6.5" fill="none" stroke="currentColor" stroke-width="1.6"/></svg>No Added<br>Sugar</span>
    <p class="benefits-line">Benefits:<br>High fibre | Digestive Support | Healthy fats</p>
  </div>

  <div class="brand" style="position:absolute;left:30px;top:300px;font-size:20px">
    <span class="brand__name"><span class="brand__dot"></span>BRAMBLE</span>
    <span style="font-size:13px;letter-spacing:1.5px">NUTRITION</span>
  </div>
  <h1 class="title" style="position:absolute;left:180px;top:220px;font-size:44px">Maple &amp;<br>Vanilla<br>Granola</h1>
  <p class="subtitle" style="position:absolute;left:180px;top:362px">WITH COCONUT &amp; DRIED CRANBERRIES</p>
  <span class="net-vertical" style="left:352px;top:334px">40G NET</span>

  <div class="claims" style="position:absolute;left:26px;top:402px;gap:14px">
    <span class="claim"><svg width="18" height="18" viewBox="0 0 18 18"><circle cx="9" cy="9" r="8" fill="none" stroke="currentColor" stroke-width="1.6"/><path d="M9 4.5a3 3 0 0 1 3 3c0 2.3-3 5.5-3 5.5s-3-3.2-3-5.5a3 3 0 0 1 3-3z" fill="currentColor"/></svg>Locally<br>Made</span>
    <span class="claim"><svg width="18" height="18" viewBox="0 0 18 18"><circle cx="9" cy="9" r="8" fill="none" stroke="currentColor" stroke-width="1.6"/><path d="M5 9.5l2.6 2.5L13 6.5" fill="none" stroke="currentColor" stroke-width="1.6"/></svg>Made by a<br>Nutritionist</span>
  </div>
  <p style="position:absolute;left:238px;top:400px;font-size:10px;font-weight:700;line-height:1.2">Ingredients<br><span style="font-size:7.5px;font-weight:400">Coconut, Apricots, Almonds, Coconut</span></p>

  <table class="nutrition" style="left:36px;top:458px;width:138px">
    <caption>THE GOODNESS YOU'RE RECEIVING<br><span style="font-weight:400">Servings Per Pack: 1 &nbsp; Serving Size: 40g NET</span></caption>
    <tr><th></th><th>Avg Qty<br>Per Serving</th><th>Avg Qty<br>Per 100g</th></tr>
    <tr><td>Energy</td><td>752kJ (180Cal)</td><td>1880kJ (450Cal)</td></tr>
    <tr><td>Protein</td><td>3.3g</td><td>8.2g</td></tr>
    <tr><td>Fat, Total</td><td>13.2g</td><td>33.0g</td></tr>
    <tr><td>– Saturated</td><td>6.7g</td><td>16.7g</td></tr>
    <tr><td>Carbohydrate</td><td>9.9g</td><td>24.8g</td></tr>
    <tr><td>– Sugars</td><td>9.7g</td><td>24.2g</td></tr>
    <tr><td>Dietary Fibre</td><td>5.6g</td><td>14g</td></tr>
    <tr><td>Sodium</td><td>8mg</td><td>20mg</td></tr>
  </table>

  <p class="fine" style="left:182px;top:458px;width:175px"><b>THE GOODNESS YOU'RE EATING</b><br>Dried Apricot (37%), Almond Meal (25%), Desiccated Coconut (25%), Maple Syrup (7%), Coconut Oil (1%), Vanilla Extract (1%).<br><br>Made with in Canberra, Australia<br><br>Store in a cool, dry place<br>and out of direct sunlight</p>
  <div class="badge" style="left:262px;top:548px;width:78px;height:20px" role="img" aria-label="country of origin badge"></div>
  <p class="fine" style="left:262px;top:572px;font-size:5px;line-height:1.2">Bramble Nutrition<br>14 Wattle Lane, Kingston ACT 2604</p>
</section>

<!-- Cereal bag front artwork -->
<section class="panel panel--cereal" aria-label="Cereal bag front artwork">
  <div class="deco deco--nut" style="left:110px;top:-18px;width:100px;height:55px" role="img" aria-label="almond outline illustration"></div>
  <div class="deco deco--seeds" style="left:270px;top:0;width:110px;height:70px" role="img" aria-label="seed scatter illustration"></div>
  <div class="deco deco--nut" style="left:380px;top:-14px;width:80px;height:50px" role="img" aria-label="almond outline illustration"></div>
  <div class="deco deco--seeds" style="left:395px;top:60px;width:70px;height:130px" role="img" aria-label="seed scatter illustration"></div>
  <div class="deco deco--berry" style="left:10px;top:200px;width:62px;height:62px" role="img" aria-label="cranberry illustration"></div>
  <div class="deco deco--slice" style="left:-40px;top:440px;width:90px;height:130px" role="img" aria-label="apricot slice outline illustration"></div>
  <div class="deco deco--berry" style="left:400px;top:430px;width:62px;height:80px" role="img" aria-label="cranberry illustration"></div>

  <div class="stamp" style="left:48px;top:82px;width:56px;height:56px" role="img" aria-label="locally made seal"></div>
  <div class="brand" style="position:absolute;left:32px;top:168px;font-size:26px;gap:3px">
    <span class="brand__name"><span class="brand__dot"></span>BRAMBLE</span>
    <span style="font-size:15px;letter-spacing:2px">NUTRITION</span>
  </div>
  <h1 class="title" style="position:absolute;left:210px;top:98px;font-size:60px">Maple &amp;<br>Vanilla<br>Granola</h1>
  <p class="subtitle" style="position:absolute;left:212px;top:280px;font-size:10px">WITH COCONUT &amp; DRIED CRANBERRIES</p>

  <svg style="position:absolute;left:60px;top:320px" width="340" height="180" viewBox="0 0 340 180" role="img" aria-label="clear window showing the granola inside">
    <path d="M20 4 Q170 -6 320 4 Q336 6 336 22 L336 140 Q336 156 318 160 Q170 186 22 160 Q4 156 4 140 L4 22 Q4 6 20 4 Z" fill="var(--window)" stroke="var(--plum)" stroke-width="4"/>
  </svg>

  <p class="blurb" style="left:70px;top:518px;width:120px">Sweet, chewy &amp; delicious, our apricot &amp; coconut energy balls are filled with dried apricots, almonds, coconut &amp; a touch of maple syrup &amp; vanilla.<br><br>Made in small batches, &amp; full of fibre. These energy balls make for a deliciously healthy snack.</p>
  <div class="benefits" style="left:200px;top:516px;width:180px;border-left:1px solid var(--ink);padding-left:8px">
    <h4>BENEFITS:</h4>
    <ul><li>High fibre</li><li>Sustained Energy</li><li>Digestive Support</li><li>Antioxidants</li><li>Healthy fats</li><li>Immunity</li></ul>
  </div>
  <div class="claims" style="position:absolute;left:200px;top:576px;gap:12px">
    <span class="claim claim--stacked"><svg width="22" height="22" viewBox="0 0 18 18"><circle cx="9" cy="9" r="8" fill="none" stroke="currentColor" stroke-width="1.6"/><path d="M5 9.5l2.6 2.5L13 6.5" fill="none" stroke="currentColor" stroke-width="1.6"/></svg>High<br>Fiber</span>
    <span class="claim claim--stacked"><svg width="22" height="22" viewBox="0 0 18 18"><circle cx="9" cy="9" r="8" fill="none" stroke="currentColor" stroke-width="1.6"/><path d="M5 9.5l2.6 2.5L13 6.5" fill="none" stroke="currentColor" stroke-width="1.6"/></svg>Gluten<br>Free</span>
    <span class="claim claim--stacked"><svg width="22" height="22" viewBox="0 0 18 18"><circle cx="9" cy="9" r="8" fill="none" stroke="currentColor" stroke-width="1.6"/><path d="M5 9.5l2.6 2.5L13 6.5" fill="none" stroke="currentColor" stroke-width="1.6"/></svg>Vegan<br>&nbsp;</span>
    <span class="claim claim--stacked"><svg width="22" height="22" viewBox="0 0 18 18"><circle cx="9" cy="9" r="8" fill="none" stroke="currentColor" stroke-width="1.6"/><path d="M5 9.5l2.6 2.5L13 6.5" fill="none" stroke="currentColor" stroke-width="1.6"/></svg>No Added<br>Sugar</span>
  </div>
  <p class="net" style="left:205px;top:632px">630G NET</p>
</section>

</body>
</html>
```